Venture 482 - Lumora Book Cover

I am looking for a Lumora book cover for my book about "Venture 482".
The Book is Titled:
Venture 482 Ascended
Shaping Outcomes: Paths To Unlocking Cosmic Truths
Author is Dorian Pell
Here is a book description that may help you understand more about it:
Inspired by the genius of Edwin Marlowe, this comprehensive guide delves into the ancient wisdom and cutting-edge science behind the 482 method, a powerful tool for manifesting your desires. Whether you're seeking personal growth, financial success, or spiritual enlightenment, this book provides advanced techniques and methods to transform your dreams into reality.
Any questions please ask.
Thanks
Owen

```html
<!DOCTYPE html>
<html lang="en">
<head>
<meta charset="utf-8">
<title>Venture 482 Ascended — Dorian Pell</title>
<link href="https://fonts.googleapis.com/css2?family=Julius+Sans+One&family=Poppins:wght@700;800&family=Montserrat:wght@400;800&display=swap" rel="stylesheet">
<style>
  :root {
    --sky-top: #4f1a3e;
    --sky-upper: #874068;
    --cloud-pink: #c98fb2;
    --haze-blue: #a9c4dc;
    --floor-pink: #c8508c;
    --floor-deep: #9a2a6c;
    --tower-shade: rgba(120, 30, 85, 0.75);
    --tower-light: rgba(225, 170, 200, 0.45);
    --author: #f7e6de;
    --title-cream: #fdefe2;
    --number-ice: #e7f3fc;
    --edition-blue: #3e4893;
    --subtitle: #ffffff;
  }
  * { margin: 0; padding: 0; box-sizing: border-box; }
  html, body { width: 805px; height: 1200px; overflow: hidden; background: #ffffff; }
  .cover {
    position: relative;
    width: 805px;
    height: 1200px;
    overflow: hidden;
  }
  .cover-art {
    position: absolute;
    inset: 0;
    background:
      radial-gradient(ellipse 120px 40px at 405px 1020px, rgba(90, 20, 70, 0.35), rgba(90, 20, 70, 0) 100%),
      linear-gradient(90deg,
        var(--tower-shade) 0%, var(--tower-light) 9%, var(--tower-shade) 15.5%,
        rgba(150, 60, 110, 0) 17%, rgba(150, 60, 110, 0) 83%,
        var(--tower-shade) 84.5%, var(--tower-light) 92%, var(--tower-shade) 100%),
      radial-gradient(ellipse 260px 120px at 300px 230px, rgba(230, 170, 200, 0.35), rgba(230, 170, 200, 0) 100%),
      radial-gradient(ellipse 300px 140px at 520px 900px, rgba(240, 160, 200, 0.45), rgba(240, 160, 200, 0) 100%),
      linear-gradient(180deg,
        var(--sky-top) 0%, var(--sky-upper) 18%, var(--cloud-pink) 40%,
        var(--cloud-pink) 56%, var(--haze-blue) 64%, var(--haze-blue) 68%,
        #d79ac0 73%, var(--floor-pink) 84%, var(--floor-deep) 100%);
  }
  .author {
    position: absolute;
    top: 76px;
    left: 0;
    width: 100%;
    text-align: center;
    font-family: "Julius Sans One", sans-serif;
    font-size: 48px;
    line-height: 1;
    letter-spacing: 0.55em;
    padding-left: 0.55em;
    color: var(--author);
  }
  .title {
    position: absolute;
    left: 0;
    width: 100%;
    text-align: center;
    font-family: "Poppins", sans-serif;
  }
  .title-word {
    top: 232px;
    font-size: 108px;
    font-weight: 800;
    line-height: 1;
    letter-spacing: -0.03em;
    color: var(--title-cream);
    text-shadow: 0 4px 10px rgba(60, 20, 50, 0.35);
  }
  .title-number {
    top: 316px;
    font-size: 288px;
    font-weight: 700;
    line-height: 1;
    letter-spacing: -0.02em;
    color: var(--number-ice);
    text-shadow: 0 8px 18px rgba(60, 20, 60, 0.35);
  }
  .edition {
    position: absolute;
    top: 592px;
    left: 0;
    width: 100%;
    text-align: center;
    font-family: "Montserrat", sans-serif;
    font-weight: 800;
    font-size: 60px;
    letter-spacing: 0.27em;
    padding-left: 0.27em;
    line-height: 1;
    color: var(--edition-blue);
  }
  .subtitle {
    position: absolute;
    top: 1040px;
    left: 0;
    width: 790px;
    text-align: center;
    font-family: "Montserrat", sans-serif;
    font-weight: 400;
    color: var(--subtitle);
  }
  .subtitle-lead {
    font-size: 31px;
    line-height: 1.25;
    text-transform: uppercase;
  }
  .subtitle-line {
    font-size: 32px;
    line-height: 1.15;
  }
</style>
</head>
<body>
  <main class="cover">
    <div class="cover-art" role="img" aria-label="Surreal pink and magenta skyline: tall apartment towers rise on both sides and hang mirrored from above, with a lone hooded figure standing on a reflective cloud floor"></div>
    <p class="author">DORIAN PELL</p>
    <h1>
      <span class="title title-word">VENTURE</span>
      <span class="title title-number">482</span>
    </h1>
    <p class="edition">ASCENDED</p>
    <div class="subtitle">
      <p class="subtitle-lead">Shaping Outcomes:</p>
      <p class="subtitle-line">Paths to unlocking</p>
      <p class="subtitle-line">cosmic truths</p>
    </div>
  </main>
</body>
</html>
```